Renewed electronic office supplies

I need a landing page design for a B2B business that will sell refurbished and renewed electronic devices such as smartphones, laptops, tablets and other gadgets. We want to become suppliers of these devices to companies that need computers and other devices for their employees. The point of our business is that they can get a great device that is in very good contrition instead of buying brand new. Companies will be able to save 50-60% on these renewed devices. Not only that we will also buy the companies old devices which they no longe needs and renew them and give them new life so we can resell it.

Our services will be:

- sale of renewed devices with lifetime warranty

- purchase of old devices

- swap solution: meaning client buy from us and sell at the same time so we deduct the amount sale of their old devices into their purchase.

Some useful information:

- company name and logo are still pending

- we aim to provide all business with top quality of renewed and environmentally friendly electronics, while maintaining a minimal impact on the natural environment.

I have attached a word document with some additional info that might be useful

Looking forward to seeing all your great designs!

P.s. Please feel free to make designs that are not based on my documents also, we need different layouts and designs. as for now I see many of the designs are more or less the same. we need more variation on design

Target Market(s)

Medium to large Businesses

Industry/Entity Type

Technology Equipment

Requirements
Must have
• we need more designs to be submitted , 50 designs minimum

```html
<!DOCTYPE html>
<html lang="en">
<head>
<meta charset="utf-8">
<title>Circuvia International – Renewed Electronic Office Supplies</title>
<link href="https://fonts.googleapis.com/css2?family=IBM+Plex+Sans:wght@400;500;600;700&display=swap" rel="stylesheet">
<style>
  :root {
    --navy: #10264f;
    --green: #1fc463;
    --white: #ffffff;
    --section-grey: #f4f1f2;
    --text: #2b2b33;
    --card-border: #c9cbd3;
    --footer-line: #3a5088;
  }
  * { margin: 0; padding: 0; box-sizing: border-box; }
  html, body { width: 672px; height: 1200px; overflow: hidden; background: var(--white); }
  body { font-family: "IBM Plex Sans", Arial, sans-serif; color: var(--text); }
  .page { position: relative; width: 672px; height: 1200px; overflow: hidden; }
  .abs { position: absolute; }

  /* Hero */
  .hero-shape { position: absolute; left: 0; top: 0; }
  .brand { position: absolute; font-weight: 600; font-size: 13px; color: var(--white); letter-spacing: 0.1px; }
  .main-nav { position: absolute; top: 17px; left: 0; width: 672px; height: 12px; }
  .main-nav a { position: absolute; font-size: 7.5px; font-weight: 600; color: var(--white); text-decoration: none; letter-spacing: 0.2px; }
  .main-nav a.active { color: var(--green); }
  .hero-title { position: absolute; left: 71px; top: 112px; font-size: 18px; line-height: 23.5px; font-weight: 700; color: var(--white); letter-spacing: 0.3px; }
  .hero-text { position: absolute; left: 72px; top: 171px; width: 220px; font-size: 9.6px; line-height: 12.5px; color: var(--white); }
  .shop-btn { position: absolute; left: 73px; top: 241px; width: 89px; height: 27px; border-radius: 14px; background: var(--green); }
  .shop-btn span { position: absolute; left: 16px; top: 7px; font-size: 10.5px; font-weight: 700; color: var(--white); letter-spacing: 0.3px; }
  .shop-btn svg { position: absolute; left: 64px; top: 4px; }
  .save-note { position: absolute; left: 73px; top: 347px; font-size: 7.5px; font-weight: 700; color: var(--white); letter-spacing: 0.2px; }

  /* Categories */
  .category { position: absolute; top: 396px; width: 124px; height: 120px; border-radius: 4px; overflow: hidden; }
  .category .label { position: absolute; left: 0; bottom: 10px; width: 100%; text-align: center; font-size: 9.5px; font-weight: 600; color: var(--white); letter-spacing: 0.2px; }
  .cat-phones { background: radial-gradient(circle at 50% 45%, #0f6a86 0%, #0a2a5a 55%, #061436 100%); }
  .cat-laptops { background: linear-gradient(180deg, #6f6f73 0%, #5a5658 60%, #4a4340 100%); }
  .cat-tablets { background: linear-gradient(160deg, #8c8a8c 0%, #4f4d52 45%, #a58a74 100%); }
  .cat-gadgets { background: linear-gradient(135deg, #0d4c8e 0%, #2a5ca8 45%, #8a3a8f 80%, #c8346c 100%); }

  /* About */
  .about { position: absolute; left: 0; top: 546px; width: 672px; height: 282px; background: var(--section-grey); }
  .eyebrow { position: absolute; left: 72px; top: 576px; font-size: 7.5px; font-weight: 700; color: var(--navy); }
  .about-title { position: absolute; left: 72px; top: 588px; font-size: 12.5px; line-height: 16.5px; font-weight: 700; color: var(--navy); letter-spacing: 0.2px; }
  .about-copy { position: absolute; left: 72px; width: 255px; font-size: 8px; line-height: 9.8px; color: var(--text); }
  .about-copy h3 { font-size: 8px; font-weight: 700; color: var(--navy); line-height: 10px; }
  .phones-visual { position: absolute; left: 363px; top: 579px; }

  /* Services */
  .section-title { position: absolute; left: 0; top: 854px; width: 672px; text-align: center; font-size: 12.5px; font-weight: 700; color: var(--navy); letter-spacing: 0.3px; }
  .title-rule { position: absolute; left: 323px; top: 876px; width: 26px; height: 1.5px; background: var(--green); }
  .service { position: absolute; top: 901px; width: 124px; height: 168px; border: 1px solid var(--card-border); border-radius: 5px; background: var(--white); }
  .service svg { position: absolute; left: 42px; top: 20px; }
  .service p { position: absolute; left: 8px; top: 77px; width: 106px; text-align: center; font-size: 7px; line-height: 10.7px; font-weight: 500; color: #222; text-transform: uppercase; }

  /* Footer */
  .footer { position: absolute; left: 0; top: 1101px; width: 672px; height: 99px; background: var(--navy); }
  .footer-nav a { position: absolute; top: 1125px; font-size: 7.5px; color: var(--white); text-decoration: none; }
  .footer-rule { position: absolute; left: 75px; top: 1156px; width: 520px; height: 1px; background: var(--footer-line); }
  .copyright { position: absolute; left: 0; top: 1177px; width: 672px; text-align: center; font-size: 6.5px; color: var(--white); }
</style>
</head>
<body>
<div class="page">

  <!-- Hero background -->
  <svg class="hero-shape" width="672" height="370" viewBox="0 0 672 370">
    <path d="M0 0 H672 V26 L470 214 Q400 300 372 328 Q350 340 300 342 H0 Z" fill="var(--navy)"/>
    <path d="M0 342 H300 Q345 340 372 320 Q350 352 300 360 Q292 361 285 361 H0 Z" fill="var(--green)"/>
  </svg>

  <div class="brand" style="left:72px; top:14px;">Circuvia International</div>
  <nav class="main-nav">
    <a class="active" style="left:391px;">HOME</a>
    <a style="left:433px;">ABOUT US</a>
    <a style="left:491px;">SERVICES</a>
    <a style="left:548px;">CONTACT US</a>
  </nav>

  <h1 class="hero-title">REUSABLE ELECTRONIC<br>OFFICE SUPPLIES</h1>
  <p class="hero-text">we aim to provide all business with top quality of reused and environmentally friendly electronics, while maintaining a minimal impact on the natural environment.</p>
  <div class="shop-btn">
    <span>SHOP</span>
    <svg width="19" height="19" viewBox="0 0 19 19">
      <circle cx="9.5" cy="9.5" r="9.5" fill="var(--navy)"/>
      <path d="M8 5.5 L12 9.5 L8 13.5" fill="none" stroke="var(--white)" stroke-width="1.5" stroke-linecap="round" stroke-linejoin="round"/>
    </svg>
  </div>

  <svg class="abs" style="left:300px; top:84px;" width="312" height="252" viewBox="300 84 312 252" role="img" aria-label="Tilted smartphone showing a sunset mountain lake on its screen">
    <defs>
      <linearGradient id="heroPhone" x1="0" y1="0" x2="1" y2="1">
        <stop offset="0" stop-color="#1b2130"/>
        <stop offset="0.45" stop-color="#6a3a3a"/>
        <stop offset="0.55" stop-color="#c9683d"/>
        <stop offset="0.7" stop-color="#2a2633"/>
        <stop offset="1" stop-color="#0c0d12"/>
      </linearGradient>
    </defs>
    <polygon points="486,90 604,94 420,330 307,310" fill="url(#heroPhone)" stroke="#d9d9dc" stroke-width="4" stroke-linejoin="round"/>
  </svg>

  <div class="save-note">SAVE 50-60% ON THESE RENEWED DEVICES</div>

  <!-- Categories -->
  <div class="category cat-phones" style="left:73px;" role="img" aria-label="Smartphone on a dark blue background"><span class="label">SMARTPHONES</span></div>
  <div class="category cat-laptops" style="left:206px;" role="img" aria-label="Laptop on a desk"><span class="label">LAPTOPS</span></div>
  <div class="category cat-tablets" style="left:339px;" role="img" aria-label="Hands using a tablet"><span class="label">TABLETS</span></div>
  <div class="category cat-gadgets" style="left:473px;" role="img" aria-label="Headphones, keyboard, mouse and game controller"><span class="label">GADGETS</span></div>

  <!-- About -->
  <section class="about"></section>
  <div class="eyebrow">WE ARE</div>
  <h2 class="about-title">A SMARTER CIRCULAR SOLUTION<br>FOR ELECTRONIC SUPPLIES</h2>
  <p class="about-copy" style="top:632px; width:240px;">Billions of electronics are being made, sold, and disposed of every year – a cycle that drives short-term profits for electronics manufacturers, but at too high a cost for the planet we all share. With our experience in the recycling market we can put an end to this cycle and offer a circular solution that is both affordable and environmentally friendly.</p>
  <div class="about-copy" style="top:704px;">
    <h3>Buy reusable IT</h3>
    We specialize in refurbished electronic devices with top quality for affordable prices. All our products have undergone a detailed testing and reconditioning program by expert technicians.
  </div>
  <div class="about-copy" style="top:753px;">
    <h3>Sell your IT Safely</h3>
    We can also buy your used electronics and make sure they get reused and give them a new life. By selling your used devices that you no longer have use for you can help us create carbon savings.
  </div>
  <svg class="phones-visual" width="193" height="249" viewBox="0 0 193 249" role="img" aria-label="Two smartphones with purple flower lock screens">
    <defs>
      <linearGradient id="phoneA" x1="0" y1="0" x2="0" y2="1">
        <stop offset="0" stop-color="#c455d6"/>
        <stop offset="0.45" stop-color="#6a3fb8"/>
        <stop offset="1" stop-color="#2a1a6a"/>
      </linearGradient>
      <linearGradient id="phoneB" x1="0" y1="0" x2="0" y2="1">
        <stop offset="0" stop-color="#9a6ae6"/>
        <stop offset="0.5" stop-color="#8a78d8"/>
        <stop offset="1" stop-color="#4a3a8a"/>
      </linearGradient>
    </defs>
    <path d="M14 0 H92 Q104 2 104 16 V249 H0 V14 Q0 0 14 0 Z" fill="url(#phoneA)" stroke="#1c1c22" stroke-width="4"/>
    <path d="M98 67 H178 Q192 67 192 81 V249 H84 V81 Q84 67 98 67 Z" fill="url(#phoneB)" stroke="#1c1c22" stroke-width="4"/>
  </svg>

  <!-- Services -->
  <h2 class="section-title">OUR SERVICES</h2>
  <div class="title-rule"></div>

  <div class="service" style="left:74px;">
    <svg width="40" height="36" viewBox="0 0 40 36">
      <path d="M5 4 Q14 0 20 0 Q26 0 35 4 V18 Q35 28 20 35 Q5 28 5 18 Z" fill="var(--navy)"/>
      <path d="M9 7 Q15 4 20 4 Q25 4 31 7 V18 Q31 25 20 31 Q9 25 9 18 Z" fill="var(--white)"/>
      <path d="M12 17 L19 25 L33 6" fill="none" stroke="var(--navy)" stroke-width="3.5" stroke-linecap="round" stroke-linejoin="round"/>
    </svg>
    <p>Sale of renewed devices with lifetime warranty</p>
  </div>
  <div class="service" style="left:206px;">
    <svg width="40" height="36" viewBox="0 0 40 36">
      <rect x="10.5" y="0.5" width="19" height="35" rx="3" fill="var(--navy)"/>
      <rect x="13" y="4" width="14" height="25" fill="var(--white)"/>
      <rect x="17" y="1.5" width="6" height="1.3" rx="0.6" fill="var(--white)"/>
      <circle cx="20" cy="32" r="1.5" fill="var(--white)"/>
    </svg>
    <p>Purchase of old devices</p>
  </div>
  <div class="service" style="left:339px;">
    <svg width="40" height="36" viewBox="0 0 40 36">
      <path d="M11 10 Q11 2 20 2 Q29 2 29 10" fill="none" stroke="var(--navy)" stroke-width="3"/>
      <rect x="1" y="10" width="38" height="5" rx="1.5" fill="var(--navy)"/>
      <path d="M3 15 H37 L34 35 H6 Z" fill="var(--navy)"/>
      <g fill="var(--white)">
        <rect x="7" y="18" width="5.5" height="6"/><rect x="14.5" y="18" width="5" height="6"/><rect x="21.5" y="18" width="5" height="6"/><rect x="28.5" y="18" width="5" height="6"/>
        <rect x="8" y="26" width="4.5" height="6"/><rect x="14.5" y="26" width="5" height="6"/><rect x="21.5" y="26" width="5" height="6"/><rect x="28.5" y="26" width="4" height="6"/>
      </g>
    </svg>
    <p>Swap solution: meaning clients buy from us and sell at the same time so we deduct the amount sale of their old devices into their purchase.</p>
  </div>
  <div class="service" style="left:474px;">
    <svg width="40" height="36" viewBox="0 0 40 36">
      <g fill="none" stroke="var(--navy)" stroke-width="4" stroke-linejoin="round">
        <path d="M14 12 L20 2 L26 12"/>
        <path d="M31 18 L37 30 H26"/>
        <path d="M14 30 H3 L9 20"/>
      </g>
      <g fill="var(--navy)">
        <path d="M23 13 L31 11 L29 19 Z"/>
        <path d="M24 26 L20 32 L27 34 Z"/>
        <path d="M5 16 L12 19 L7 24 Z"/>
      </g>
    </svg>
    <p>We aim to provide all businesses with top quality of renewed and environmentally friendly electronics, while maintaining a minimal impact on the natural environment.</p>
  </div>

  <!-- Footer -->
  <footer class="footer"></footer>
  <div class="brand" style="left:74px; top:1121px;">Circuvia International</div>
  <nav class="footer-nav">
    <a style="left:393px;">HOME</a>
    <a style="left:434px;">ABOUT US</a>
    <a style="left:492px;">SERVICES</a>
    <a style="left:547px;">CONTACT US</a>
  </nav>
  <div class="footer-rule"></div>
  <div class="copyright">Copyright © 2020 All Rights Reserved</div>

</div>
</body>
</html>
```